American cannabis tech company business card design

Pavrel.com is seeking a modern, professional, and brand-aligned business card that represents our company and its core values: Mission, Story, Values, and Impact. As an innovative cannabis company, we want a business card that is not only visually appealing but also serves as a representation of who we are and what we stand for.

Project Scope: Design a double-sided business card that integrates our brand identity and core values. Incorporate our key brand elements, ensuring a sleek and contemporary aesthetic. Visually reflect our core values (Mission, Story, Values, Impact) in a way that is engaging yet professional.

Target Market(s)

Vendors, third parties,

Contact Information for Business Card

Contact details (name, title, email, phone, website, etc.)

Font styles to use
Other font styles liked:
• Caslon, Centra

Colors

Designer to choose colors to be used in the design.

Requirements
Must have
• Pavrel.com logo and branding A creative yet clean way to integrate our core values (Mission, Story, Values, Impact) Modern typography and a well-structured layout
Nice to have
• forest green, grey, white, black
Should not have
• references to marijuana, leafs, plants, or related product

```html
<!DOCTYPE html>
<html lang="en">
<head>
<meta charset="utf-8">
<title>Pavrel.com Business Card</title>
<link rel="stylesheet" href="https://fonts.googleapis.com/css2?family=Poppins:wght@400;500;600;700;800&display=swap">
<style>
  :root {
    --forest: #1b3a1f;
    --paper: #fbfaf6;
    --ink: #111511;
    --stage: #d9dad7;
    --line: #3d4a3d;
  }
  * { margin: 0; padding: 0; box-sizing: border-box; }
  html, body { width: 1200px; height: 880px; overflow: hidden; }
  body {
    background: var(--stage);
    font-family: "Poppins", sans-serif;
    display: flex;
    flex-direction: column;
    align-items: center;
    justify-content: center;
    gap: 36px;
  }
  .card {
    width: 700px;
    height: 400px;
    border-radius: 22px;
    position: relative;
    overflow: hidden;
    box-shadow: 0 6px 18px rgba(0,0,0,.18);
  }

  /* Back side */
  .card-back {
    background: var(--forest);
    display: flex;
    flex-direction: column;
    align-items: center;
    justify-content: center;
    color: var(--paper);
  }
  .card-back .wordmark {
    font-weight: 800;
    font-size: 96px;
    line-height: 1;
    letter-spacing: -1px;
  }
  .card-back .site {
    margin-top: 12px;
    font-size: 15px;
    letter-spacing: 5px;
    font-weight: 400;
  }

  /* Front side */
  .card-front { background: var(--paper); color: var(--forest); }
  .card-front .wordmark {
    position: absolute;
    left: 46px;
    top: 96px;
    font-weight: 800;
    font-size: 78px;
    line-height: 1;
    letter-spacing: -1px;
  }
  .holder {
    position: absolute;
    left: 46px;
    top: 226px;
  }
  .holder-name {
    font-weight: 700;
    font-size: 21px;
    letter-spacing: .3px;
    line-height: 1.1;
  }
  .holder-title {
    font-size: 13px;
    color: var(--ink);
    line-height: 1.3;
  }
  .rule {
    position: absolute;
    left: 124px;
    right: 40px;
    top: 258px;
    height: 1px;
    background: var(--line);
  }
  .contacts {
    position: absolute;
    left: 46px;
    top: 290px;
    list-style: none;
  }
  .contacts li {
    display: flex;
    align-items: center;
    gap: 12px;
    font-size: 14px;
    color: var(--ink);
    height: 27px;
  }
  .contacts svg { width: 20px; height: 20px; flex: none; }
  .social {
    position: absolute;
    right: 40px;
    top: 206px;
    display: flex;
    gap: 7px;
  }
  .social span {
    width: 16px; height: 16px;
    border-radius: 4px;
    background: var(--forest);
  }
  .accent-band {
    position: absolute;
    right: 0;
    bottom: 0;
    width: 215px;
    height: 128px;
    background: var(--forest);
    color: var(--paper);
    display: flex;
    flex-direction: column;
    justify-content: center;
    padding-left: 26px;
  }
  .accent-notch {
    position: absolute;
    right: 223px;
    bottom: 0;
    width: 3px;
    height: 128px;
    background: var(--forest);
  }
  .core-values {
    list-style: none;
  }
  .core-values li {
    font-size: 11px;
    font-weight: 600;
    letter-spacing: 3px;
    line-height: 22px;
  }
</style>
</head>
<body>
  <section class="card card-back">
    <div class="wordmark">PAVREL</div>
    <div class="site">www.PAVREL.com</div>
  </section>

  <section class="card card-front">
    <div class="wordmark">PAVREL</div>
    <div class="social">
      <span></span><span></span><span></span>
    </div>
    <div class="holder">
      <div class="holder-name">DANA R. HOLT</div>
      <div class="holder-title">Director</div>
    </div>
    <div class="rule"></div>
    <ul class="contacts">
      <li>
        <svg viewBox="0 0 20 20"><rect width="20" height="20" rx="4" fill="#1b3a1f"/><path d="M7 5l2 3-1.2 1.2a7 7 0 0 0 3 3L12 11l3 2-1 2c-4 0-9-5-9-9z" fill="#fbfaf6"/></svg>
        +1 405 -555-0182
      </li>
      <li>
        <svg viewBox="0 0 20 20"><rect width="20" height="20" rx="4" fill="#1b3a1f"/><rect x="4.5" y="6" width="11" height="8" fill="none" stroke="#fbfaf6" stroke-width="1.3"/><path d="M4.5 6l5.5 4.5L15.5 6" fill="none" stroke="#fbfaf6" stroke-width="1.3"/></svg>
        team@pavrel.com
      </li>
      <li>
        <svg viewBox="0 0 20 20"><rect width="20" height="20" rx="4" fill="#1b3a1f"/><circle cx="10" cy="10" r="5.5" fill="none" stroke="#fbfaf6" stroke-width="1.2"/><ellipse cx="10" cy="10" rx="2.3" ry="5.5" fill="none" stroke="#fbfaf6" stroke-width="1"/><path d="M4.5 10h11" stroke="#fbfaf6" stroke-width="1"/></svg>
        www.PAVREL.com
      </li>
    </ul>
    <div class="accent-notch"></div>
    <div class="accent-band">
      <ul class="core-values">
        <li>MISSION</li>
        <li>STORY</li>
        <li>VALUES</li>
        <li>IMPACT</li>
      </ul>
    </div>
  </section>
</body>
</html>
```